Vantro cards

I am in the auto motive, transportation business I would like a business card that is Something cool, modern edgy, having to do with car culture. I offer towing service for high and exotic cars. I also provide towing for collisions and car accidents. I offer open and enclosed transport nationwide.

Target Market(s)

Car culture people high end auto collectors

Industry/Entity Type

Towing car carrier

Contact Information for Business Card

My company colors black yellow and silver

Font styles to use
Serif

```html
<!DOCTYPE html>
<html lang="en">
<head>
<meta charset="UTF-8">
<title>Vantro Transportation – Business Cards</title>
<link href="https://fonts.googleapis.com/css2?family=Arvo:wght@400;700&family=Lato:wght@400;700&display=swap" rel="stylesheet">
<style>
  :root {
    --backdrop: #161616;
    --ink: #111111;
    --yellow: #fbe264;
    --silver-light: #f3f3f3;
    --silver-mid: #dedede;
    --silver-dark: #c9c9c9;
  }
  * { box-sizing: border-box; margin: 0; padding: 0; }
  html, body {
    width: 1200px;
    height: 1122px;
    overflow: hidden;
    background: var(--backdrop);
  }
  .sheet {
    position: relative;
    width: 1200px;
    height: 1122px;
  }
  .card {
    position: absolute;
    left: 180px;
    width: 840px;
    height: 480px;
    border-radius: 30px;
    overflow: hidden;
  }
  .card--front {
    top: 60px;
    background: linear-gradient(160deg, var(--silver-dark) 0%, var(--silver-light) 45%, var(--silver-mid) 100%);
  }
  .card--back {
    top: 582px;
    background: var(--yellow);
  }
  .wordmark {
    position: absolute;
    display: flex;
    flex-direction: column;
    align-items: center;
    font-family: "Arvo", serif;
    font-weight: 700;
    color: var(--ink);
    line-height: 1;
  }
  .card--front .wordmark {
    left: 0; right: 0; top: 170px;
  }
  .wordmark__name {
    font-size: 96px;
    letter-spacing: 2px;
    text-transform: uppercase;
  }
  .wordmark__sub {
    margin-top: 14px;
    font-size: 27px;
    letter-spacing: 5px;
    text-transform: uppercase;
  }
  .back-panel {
    position: absolute;
    inset: 0;
    width: 840px;
    height: 480px;
  }
  .card--back .wordmark {
    left: 470px; right: 0; top: 160px;
  }
  .card--back .wordmark__name { font-size: 66px; }
  .card--back .wordmark__sub { font-size: 19px; letter-spacing: 3px; margin-top: 12px; }
  .contact {
    position: absolute;
    left: 62px;
    top: 188px;
    color: var(--ink);
  }
  .contact__name {
    font-family: "Arvo", serif;
    font-weight: 400;
    font-size: 36px;
    letter-spacing: 1px;
    text-transform: uppercase;
  }
  .contact__title {
    font-family: "Lato", sans-serif;
    font-size: 22px;
    margin-top: 6px;
  }
  .contact__rule {
    width: 150px;
    height: 3px;
    background: var(--ink);
    margin: 20px 0 22px;
  }
  .contact__list { list-style: none; }
  .contact__item {
    display: flex;
    align-items: center;
    gap: 14px;
    font-family: "Lato", sans-serif;
    font-size: 21px;
    margin-bottom: 10px;
  }
  .contact__item--phone { font-size: 25px; }
  .contact__icon { width: 18px; height: 18px; flex: none; }
</style>
</head>
<body>
<main class="sheet">

  <section class="card card--front" aria-label="Card front">
    <div class="wordmark">
      <span class="wordmark__name">Vantro</span>
      <span class="wordmark__sub">Transportation</span>
    </div>
  </section>

  <section class="card card--back" aria-label="Card back">
    <svg class="back-panel" viewBox="0 0 840 480" aria-hidden="true">
      <defs>
        <linearGradient id="silverPanel" x1="0" y1="0" x2="1" y2="1">
          <stop offset="0" stop-color="#f5f5f5"/>
          <stop offset="0.5" stop-color="#e6e6e6"/>
          <stop offset="1" stop-color="#d4d4d4"/>
        </linearGradient>
      </defs>
      <path class="panel-border" d="M540 -20 H860 V430 H546 L446 340 V104 Z" fill="#111"/>
      <path class="panel-face" d="M556 -20 H860 V412 H560 L466 330 V112 Z" fill="url(#silverPanel)"/>
    </svg>

    <div class="wordmark">
      <span class="wordmark__name">Vantro</span>
      <span class="wordmark__sub">Transportation</span>
    </div>

    <div class="contact">
      <h1 class="contact__name">Dean Whitlock</h1>
      <p class="contact__title">Managing Director</p>
      <div class="contact__rule"></div>
      <ul class="contact__list">
        <li class="contact__item contact__item--phone">
          <svg class="contact__icon" viewBox="0 0 24 24"><path d="M6.6 10.8a15 15 0 0 0 6.6 6.6l2.2-2.2c.3-.3.7-.4 1-.2 1.1.4 2.3.6 3.6.6.6 0 1 .4 1 1V20c0 .6-.4 1-1 1A17 17 0 0 1 3 4c0-.6.4-1 1-1h3.5c.6 0 1 .4 1 1 0 1.3.2 2.5.6 3.6.1.3 0 .7-.2 1z" fill="#111"/></svg>
          123-456-7890
        </li>
        <li class="contact__item">
          <svg class="contact__icon" viewBox="0 0 24 24"><path d="M2 5h20v14H2z" fill="#111"/><path d="M2 5l10 8 10-8" fill="none" stroke="#fbe264" stroke-width="1.8"/></svg>
          whitlock@yourwebsite.com
        </li>
        <li class="contact__item">
          <svg class="contact__icon" viewBox="0 0 24 24"><circle cx="12" cy="12" r="10" fill="#111"/><path d="M2 12h20M12 2c3 3 3 17 0 20M12 2c-3 3-3 17 0 20" fill="none" stroke="#fbe264" stroke-width="1.5"/></svg>
          www.yourwebsite.com
        </li>
      </ul>
    </div>
  </section>

</main>
</body>
</html>
```